Business Card for Vorla Parts Wholesale supplier

Hi There! I need a new business card for our company. We are specialized in selling Vorla parts, mostly we sell new LCD screens for Zelnar and Drelks. I would like to see that back in the design.

You can find the colors and logo's on our website: www.hartuvo.nl

Industry/Entity Type

Business

Contact Information for Business Card

My Details:
Tobias Lindqvist

Phone: 0031687203316
E-mail: Tobias@hartuvo.nl

Slogan: "Because Quality Matters"

Font styles to use
Sans Serif

Colors

Designer to choose colors to be used in the design.

Requirements
Must have
• A Black backside with the Hartuvo logo on it. The front side should be clean with only my contact details.
• But I'm also open for something really different or awesome!
Nice to have
• Remember that we are in the parts & repairing industry, So i'll be handing those business cards mainly to repair companies. Maybe you can do something with that thought :)

```html
<!DOCTYPE html>
<html lang="en">
<head>
<meta charset="utf-8">
<title>Hartuvo Business Card</title>
<link rel="stylesheet" href="https://fonts.googleapis.com/css2?family=Open+Sans:wght@400;600;700&display=swap">
<style>
  :root {
    --page-bg: #d8d1c9;
    --card-light: #f6f3f0;
    --card-mid: #ece6e0;
    --ink: #141414;
    --ink-soft: #2a2a2a;
    --brand-orange: #c8461e;
    --brand-orange-deep: #a8300f;
    --band-black: #161616;
  }
  * { box-sizing: border-box; margin: 0; padding: 0; }
  html, body {
    width: 1200px;
    height: 970px;
    overflow: hidden;
    background: var(--page-bg);
    font-family: "Open Sans", Arial, sans-serif;
  }
  .canvas {
    position: relative;
    width: 1200px;
    height: 970px;
  }
  .business-card {
    position: absolute;
    left: 100px;
    top: 200px;
    width: 1000px;
    height: 570px;
    border-radius: 28px;
    overflow: hidden;
    background: linear-gradient(160deg, var(--card-light) 0%, var(--card-mid) 100%);
    box-shadow: 0 18px 40px rgba(0, 0, 0, 0.18);
  }
  .brand {
    position: absolute;
    left: 48px;
    top: 80px;
    display: flex;
    align-items: center;
    gap: 24px;
  }
  .brand-square {
    width: 110px;
    height: 110px;
    background: var(--brand-orange);
  }
  .brand-name {
    font-weight: 700;
    font-size: 112px;
    line-height: 1;
    color: var(--ink);
    letter-spacing: -1px;
  }
  .holder-name {
    position: absolute;
    right: 52px;
    top: 322px;
    font-weight: 700;
    font-size: 34px;
    color: var(--brand-orange-deep);
  }
  .divider {
    position: absolute;
    left: 48px;
    right: 52px;
    top: 370px;
    height: 2px;
    background: var(--ink-soft);
  }
  .contact-list {
    position: absolute;
    left: 48px;
    top: 396px;
    list-style: none;
  }
  .contact-item {
    display: flex;
    align-items: center;
    gap: 18px;
    height: 34px;
    font-size: 28px;
    color: var(--ink-soft);
  }
  .contact-icon {
    width: 28px;
    height: 28px;
    flex: none;
  }
  .web-name { color: var(--brand-orange); }
  .slogan {
    position: absolute;
    right: 52px;
    top: 460px;
    font-weight: 600;
    font-size: 26px;
    color: var(--ink);
  }
  .bottom-bands {
    position: absolute;
    left: 0;
    bottom: 0;
    width: 1000px;
    height: 50px;
  }
</style>
</head>
<body>
<main class="canvas">
  <section class="business-card">
    <div class="brand">
      <span class="brand-square"></span>
      <span class="brand-name">Hartuvo</span>
    </div>

    <p class="holder-name">Tobias Lindqvist</p>
    <div class="divider"></div>

    <ul class="contact-list">
      <li class="contact-item">
        <svg class="contact-icon" viewBox="0 0 28 28" aria-hidden="true">
          <rect width="28" height="28" rx="5" fill="var(--brand-orange)"/>
          <path d="M9 6c1 0 2 3 2 4s-1.5 1.5-1 3c.8 2 2.2 3.4 4 4.2 1.3.5 2-1 3-1s4 1 4 2-1.5 3-3 3C11 21 7 16 7 9c0-1.5 1-3 2-3z" fill="#fff"/>
        </svg>
        <span>0031687203316</span>
      </li>
      <li class="contact-item">
        <svg class="contact-icon" viewBox="0 0 28 28" aria-hidden="true">
          <rect width="28" height="28" rx="5" fill="var(--brand-orange)"/>
          <rect x="5" y="8" width="18" height="12" fill="none" stroke="#fff" stroke-width="2"/>
          <path d="M5 8l9 7 9-7" fill="none" stroke="#fff" stroke-width="2"/>
        </svg>
        <span>Tobias@hartuvo.nl</span>
      </li>
      <li class="contact-item">
        <svg class="contact-icon" viewBox="0 0 28 28" aria-hidden="true">
          <rect width="28" height="28" rx="5" fill="var(--brand-orange)"/>
          <circle cx="14" cy="14" r="9" fill="none" stroke="#fff" stroke-width="1.8"/>
          <ellipse cx="14" cy="14" rx="4" ry="9" fill="none" stroke="#fff" stroke-width="1.5"/>
          <path d="M5 14h18M7 9h14M7 19h14" stroke="#fff" stroke-width="1.5"/>
        </svg>
        <span>www.<span class="web-name">hartuvo</span>.nl</span>
      </li>
    </ul>

    <p class="slogan">Because Quality Matters</p>

    <svg class="bottom-bands" viewBox="0 0 1000 50" preserveAspectRatio="none" aria-hidden="true">
      <defs>
        <linearGradient id="orangeBand" x1="0" x2="1" y1="0" y2="0">
          <stop offset="0" stop-color="#b63714"/>
          <stop offset="1" stop-color="#c8461e"/>
        </linearGradient>
      </defs>
      <polygon points="0,22 572,22 562,50 0,50" fill="var(--band-black)"/>
      <polygon points="592,2 1000,2 1000,50 578,50" fill="url(#orangeBand)"/>
    </svg>
  </section>
</main>
</body>
</html>
```